NEW Modern Sleek Business Card for VR Language Startup

Our startup is using VR to lead the next wave of world language education. We need a two-sided business card that introduces the larger organization (Brightloom Language Inc) and our contact info on one side and shows the product, Glimwoorld, on the other side.

Side 1 (contact info)= Brightloom Logo and Contact info (name, title, phone, email)

Side 2 (product)= Glimworld logo, text, and website
Text= Culturally Immersive Language Learning Games
Website= www.glimworld-play.com

Target Market(s)

Education, Technology

Contact Information for Business Card

Contact info will be updated upon approval of the design. For now, put this as a placeholder.

Perry Dunmore
Founder & CEO
pdunmore@quillpost-mail.net
(555)-014-2286

Font styles to use
Other font styles liked:
• Gibson and Century Gothic are the brand fonts

Requirements
Nice to have
• I would love to see cohesion between the design and colors of the two logos. I have attached a few business card designs that I like, so you can get a feel for my preferred style.

```html
<!DOCTYPE html>
<html lang="en">
<head>
<meta charset="utf-8">
<title>Brightloom Language – Business Cards</title>
<link rel="stylesheet" href="https://fonts.googleapis.com/css2?family=Lato:wght@400;700&display=swap">
<style>
  :root {
    --backdrop: #e9e6e1;
    --card-dark: #1e1e1e;
    --card-light: #ffffff;
    --ink-light: #ffffff;
    --ink-dark: #1c1c1c;
    --rule: #8a8a8a;
    --teal: #35c1d8;
    --pink: #e0356e;
    --amber: #f6a531;
    --mark: #ef5a4a;
  }
  * { margin: 0; padding: 0; box-sizing: border-box; }
  html, body { width: 1200px; height: 834px; overflow: hidden; }
  body {
    background: var(--backdrop);
    font-family: "Lato", sans-serif;
    position: relative;
  }
  .card {
    position: absolute;
    border-radius: 10px;
    box-shadow: 4px 6px 14px rgba(0,0,0,0.28);
  }
  .card--contact {
    left: 177px; top: 149px; width: 305px; height: 536px;
    background: var(--card-dark);
    color: var(--ink-light);
    text-align: center;
  }
  .card--product {
    left: 517px; top: 379px; width: 536px; height: 306px;
    background: var(--card-light);
    color: var(--ink-dark);
    text-align: center;
  }

  /* Company brand, stacked on the contact side */
  .company-mark {
    position: absolute; left: 112px; top: 96px;
    width: 82px; height: 82px; border-radius: 50%;
    background: var(--mark);
  }
  .company-name {
    position: absolute; left: 0; right: 0; top: 188px;
    font-weight: 700; color: var(--ink-light);
    text-transform: uppercase;
  }
  .company-name__main {
    display: block; font-size: 27px; line-height: 34px;
    letter-spacing: 0.12em; padding-left: 0.12em;
  }
  .company-name__sub {
    display: block; font-size: 15px; line-height: 20px; margin-top: 6px;
    letter-spacing: 0.55em; padding-left: 0.55em;
  }

  .person { position: absolute; left: 0; right: 0; top: 360px; }
  .person__name { font-size: 20px; line-height: 24px; font-weight: 700; letter-spacing: -0.01em; }
  .person__title { font-size: 12px; line-height: 16px; letter-spacing: 0.35em; margin-top: 2px; padding-left: 0.35em; }

  .icon-row {
    position: absolute; left: 79px; right: 79px; top: 409px;
    display: flex; align-items: center; gap: 3px;
  }
  .icon-row__rule { flex: 1; height: 1px; background: var(--rule); }
  .icon-row svg { width: 19px; height: 19px; display: block; }

  .contact-list {
    position: absolute; left: 0; right: 0; top: 434px;
    list-style: none; font-size: 12.5px; letter-spacing: 0.06em; line-height: 16px;
  }

  /* Product brand on the product side */
  .product-brand {
    position: absolute; left: 0; right: 0; top: 90px;
    display: flex; align-items: center; justify-content: center; gap: 16px;
  }
  .product-mark {
    width: 92px; height: 92px; border-radius: 50%;
    background: var(--mark); flex: none;
  }
  .product-name {
    font-size: 34px; font-weight: 700; letter-spacing: 0.12em;
    text-transform: uppercase; color: var(--ink-dark);
  }

  .tagline {
    position: absolute; left: 0; right: 0; top: 200px;
    font-size: 15px; letter-spacing: 0.01em;
  }
  .website {
    position: absolute; left: 0; right: 0; top: 268px;
    font-size: 14px; letter-spacing: 0.05em;
  }
  .website strong { font-weight: 700; }
</style>
</head>
<body>

<section class="card card--contact" aria-label="Contact side">
  <span class="company-mark"></span>
  <p class="company-name">
    <span class="company-name__main">Brightloom</span>
    <span class="company-name__sub">Language</span>
  </p>

  <div class="person">
    <p class="person__name">DELIA HARROW</p>
    <p class="person__title">CEO</p>
  </div>

  <div class="icon-row">
    <span class="icon-row__rule"></span>
    <svg viewBox="0 0 20 20" aria-label="Phone">
      <circle cx="10" cy="10" r="10" fill="var(--teal)"/>
      <path d="M6 8.5c0-1.5 1.8-2.5 4-2.5s4 1 4 2.5v.8h-2.2v-1h-3.6v1H6z" fill="#fff"/>
      <rect x="6.5" y="10" width="7" height="4" rx="1" fill="#fff"/>
    </svg>
    <svg viewBox="0 0 20 20" aria-label="Email">
      <circle cx="10" cy="10" r="10" fill="var(--pink)"/>
      <rect x="5.5" y="6.8" width="9" height="6.4" rx="0.8" fill="#fff"/>
      <path d="M5.7 7.2 10 10.4l4.3-3.2" fill="none" stroke="var(--pink)" stroke-width="1"/>
    </svg>
    <svg viewBox="0 0 20 20" aria-label="Website">
      <circle cx="10" cy="10" r="10" fill="var(--amber)"/>
      <g fill="none" stroke="#fff" stroke-width="0.9">
        <circle cx="10" cy="10" r="4.8"/>
        <ellipse cx="10" cy="10" rx="2" ry="4.8"/>
        <path d="M5.2 10h9.6M5.9 7.6h8.2M5.9 12.4h8.2"/>
      </g>
    </svg>
    <span class="icon-row__rule"></span>
  </div>

  <ul class="contact-list">
    <li>(555)-014-2286</li>
    <li>pdunmore@quillpost-mail.net</li>
    <li>www.glimworld-play.com</li>
  </ul>
</section>

<section class="card card--product" aria-label="Product side">
  <div class="product-brand">
    <span class="product-mark"></span>
    <span class="product-name">Glimworld</span>
  </div>
  <p class="tagline">Culturally Immersive Language Learning Games</p>
  <p class="website">www.<strong>glimworld-play</strong>.com</p>
</section>

</body>
</html>
```